Very new and innovative Web design for Property managers of Vacation rentals

We are looking for a new website design for travel agencies and property managers specialised on vacation rentals business, holiday villas and apartments.

The end users of this website are travellers who are looking for a vacation home for their next holiday: this is the reason why the website must be easy to use, attractive, professional, possibly elegant and focused on get new reservations.

This is a draft of our current website: https://intro3.kelumsito.com/
Please consider that we would like to have proposals with a totally different and innovative layout, surprise us!

These are the pages of the website:
• Homepage: feel free to redesign all the homepage as you wish, surprise us with something very new! Please consider that Property manager/Travel agencies usually want to have the opportunity to put in evidence groups of houses with specific characteristics (eg. villas with private swimming pool, apartment in big/small towns, villas with air co, etc…), destinations and tourist areas, and sometimes experiences or activities (please consider that the website layout must be suitable even if some of the previous sections are not used).
• Search page: we’d like to organise the results of the search page in three different ways:
o Grid
o Map
o List
• Property page: to illustrate the characteristics, descriptions, images, …. of the property. It is very important to put in evidence images of the property and to maintain the booking form (and the other call to action bottom – eg. whatsapp) always visible
• Custom pages: static pages composed usually by text, images and call to actions
• Contact us (general form)
• Info request (specific of a property form)
• Booking process
• Blog, organised in four pages:
o Home Page – introduction to the blog
o List of articles
o Single article
o Site Map (presentation of categories and sub-categories)

If possible, we’d prefer to receive the material in Adobe XD or similar so that we can obtain the three versions:
- smartphone
- tablet
- desktop

The website will be then developed in Bootstrap: as a result we’ll need the icons in SVG format (or the library used)

In attachment you can find the map of the website pages

```html
<!DOCTYPE html>
<html lang="en">
<head>
<meta charset="utf-8">
<title>StayNest – Exclusive Villas in Italy</title>
<link rel="stylesheet" href="https://fonts.googleapis.com/css2?family=Poppins:wght@500;600;700&family=Libre+Franklin:wght@400;500;600;700&display=swap">
<style>
:root{
  --green:#1fae6b;
  --green-dark:#178f57;
  --ink:#1c1c1c;
  --text:#3a3a3a;
  --muted:#666;
  --blush:#f5f1f1;
  --line:#d9d9d9;
  --footer:#222222;
  --white:#ffffff;
}
*{box-sizing:border-box;margin:0;padding:0}
html,body{width:1200px;height:3706px;overflow:hidden}
body{position:relative;font-family:"Libre Franklin",Arial,sans-serif;color:var(--text);background:var(--white)}
.photo{position:absolute}
h2.section-title{position:absolute;left:0;width:1200px;text-align:center;font-family:"Poppins",sans-serif;font-weight:700;font-size:22px;color:var(--ink);letter-spacing:-.2px}
.rule{position:absolute;height:3px;width:46px;background:var(--green)}

/* hero */
.hero{position:absolute;left:0;top:0;width:1200px;height:672px;overflow:hidden;
  background:linear-gradient(180deg,#3a3e44 0%,#6b4b3a 18%,#8a5a3d 32%,#5d4a3e 52%,#3f4a34 72%,#2d3a27 100%)}
.hero .glow{position:absolute;inset:0;background:radial-gradient(ellipse 40% 30% at 75% 20%,rgba(236,140,60,.55),transparent 70%),radial-gradient(ellipse 35% 40% at 15% 45%,rgba(200,120,70,.35),transparent 70%)}
.brand{position:absolute;display:flex;align-items:center;gap:12px;font-family:"Poppins",sans-serif;font-weight:500;color:var(--white)}
.brand .mark{width:40px;height:40px;border-radius:50%;background:var(--green)}
.nav{position:absolute;top:36px;left:0;width:1200px;height:16px;font-family:"Libre Franklin",sans-serif;font-weight:600;font-size:13.5px;color:var(--white);letter-spacing:.3px}
.nav a{position:absolute;color:inherit;text-decoration:none;white-space:nowrap}
.nav a.active{color:var(--green)}
.nav .cta{top:-7px;left:1039px;width:124px;height:30px;border:2px solid var(--green);color:var(--green);text-align:center;line-height:26px}
.hero h1{position:absolute;top:258px;left:0;width:1200px;text-align:center;font-family:"Poppins",sans-serif;font-weight:700;font-size:36px;color:var(--white);letter-spacing:-.3px}
.field{position:absolute;top:350px;height:49px;background:var(--white);font-size:12.5px;font-weight:600;color:#333;padding-left:18px;line-height:49px;letter-spacing:.3px}
.field svg{position:absolute;right:16px;top:17px}
.search-btn{position:absolute;left:531px;top:448px;width:140px;height:47px;background:var(--green);border:2px solid rgba(255,255,255,.75);color:var(--white);font-family:"Poppins",sans-serif;font-weight:700;font-size:19px;text-align:center;line-height:43px;letter-spacing:.5px}
.dots{position:absolute;top:619px;left:565px;display:flex;gap:11px}
.dots span{width:6px;height:6px;border-radius:50%;background:var(--white)}
.dots span.on{background:var(--green)}

/* rentals */
.arrow-box{position:absolute;top:984px;width:28px;height:28px;border:1px solid #cfcfcf;background:var(--white)}
.arrow-box svg{position:absolute;left:9px;top:8px}
.rental{position:absolute;top:803px;width:295px;height:390px;border:1px solid var(--line);background:var(--white);overflow:hidden}
.rental .photo{left:0;top:0;width:295px;height:193px}
.rental h3{position:absolute;left:27px;top:220px;font-size:13.5px;font-weight:700;color:var(--ink);letter-spacing:.3px}
.rental ul{position:absolute;left:27px;top:246px;list-style:none;font-size:11.5px;line-height:19.3px;color:#444}
.btn-small{position:absolute;background:var(--green);color:var(--white);font-size:10px;font-weight:700;letter-spacing:.4px;text-align:center;line-height:22px;height:22px}
.rental .btn-small{left:27px;top:336px;width:91px}
.price{position:absolute;right:0;bottom:0;width:82px;height:60px;background:var(--green);border-top-left-radius:48px;color:var(--white);text-align:right;padding:14px 7px 0 0}
.price b{display:block;font-size:17px;font-weight:600;line-height:17px}
.price small{font-size:10.5px;opacity:.9}

/* holiday */
.holiday{position:absolute;left:0;top:1255px;width:1200px;height:532px;background:var(--blush)}
.holiday h2{position:absolute;left:633px;top:44px;font-family:"Poppins",sans-serif;font-weight:700;font-size:20.5px;color:var(--ink);letter-spacing:-.2px}
.holiday .rule{left:633px;top:81px;width:97px}
.checks{position:absolute;left:633px;top:115px;width:440px;list-style:none;font-size:14.5px;line-height:21px;color:#333}
.checks li{position:absolute;left:0;padding-left:33px;white-space:nowrap}
.checks svg{position:absolute;left:4px;top:5px}

/* features */
.feature{position:absolute;width:455px;height:166px;border:3px solid #e3e3e3;background:var(--white)}
.feature .icon{position:absolute;left:32px;width:84px;height:84px;border-radius:50%;background:var(--green)}
.feature .icon svg{position:absolute;left:22px;top:22px}
.feature h3{position:absolute;left:142px;top:35px;font-size:15.5px;font-weight:700;color:var(--ink);letter-spacing:.3px;white-space:nowrap}
.feature p{position:absolute;left:142px;top:61px;width:250px;font-size:13px;line-height:19px;color:#333}
.skyline{position:absolute;left:0;top:2216px;width:1200px;height:197px;background:linear-gradient(180deg,#ffffff 0%,#f1efef 55%,#e9e6e6 100%)}

/* blog */
.blog{position:absolute;left:0;top:2413px;width:1200px;height:940px;background:var(--blush)}
.feature-post{position:absolute;left:132px;top:134px;width:602px;height:384px;background:linear-gradient(160deg,#6f8a5a 0%,#a8a079 35%,#8d6a4d 60%,#3e4a2e 100%)}
.feature-post .shade{position:absolute;left:0;bottom:0;width:100%;height:130px;background:linear-gradient(180deg,transparent,rgba(0,0,0,.7))}
.feature-post .date{position:absolute;left:27px;top:306px;font-size:12.5px;color:#eee}
.feature-post h3{position:absolute;left:27px;top:327px;font-family:"Poppins",sans-serif;font-weight:700;font-size:18px;color:var(--white);white-space:nowrap}
.feature-post p{position:absolute;left:27px;top:353px;font-size:13px;color:#eee}
.green-post{position:absolute;left:753px;top:134px;width:315px;height:384px;background:var(--green)}
.green-post .photo{left:0;top:0;width:315px;height:209px}
.green-post h3{position:absolute;left:26px;top:233px;font-family:"Poppins",sans-serif;font-weight:700;font-size:14.5px;color:var(--white);white-space:nowrap}
.green-post p{position:absolute;left:26px;top:263px;width:270px;font-size:13px;line-height:18px;color:#eafaf1}
.green-post .btn-small{left:26px;top:326px;width:80px;background:var(--white);color:var(--green)}
.post{position:absolute;top:541px;height:356px;background:var(--white)}
.post .photo{left:0;top:0;width:100%;height:187px}
.post .date{position:absolute;left:26px;top:215px;font-size:10.5px;color:#444}
.post h4{position:absolute;left:26px;top:235px;font-size:12.5px;font-weight:700;color:var(--ink);letter-spacing:.3px;white-space:nowrap}
.post p{position:absolute;left:26px;top:262px;width:245px;font-size:12px;line-height:18px;color:#333}
.post .btn-small{left:26px;top:312px;width:80px}

/* footer */
.footer{position:absolute;left:0;top:3353px;width:1200px;height:353px;background:var(--footer);color:#ddd}
.footer h5{position:absolute;top:52px;font-size:12.5px;font-weight:700;color:var(--white);letter-spacing:.5px}
.footer .menu{position:absolute;left:509px;top:89px;list-style:none;font-size:11.5px;line-height:20px;color:#ddd}
.contact-row{position:absolute;font-size:11.5px;line-height:15.5px;color:#ddd;padding-left:32px;white-space:nowrap}
.contact-row .dot{position:absolute;left:0;top:2px;width:23px;height:23px;border-radius:50%;background:var(--white)}
.contact-row .dot svg{position:absolute;left:6px;top:6px}
.footer .divider{position:absolute;left:131px;top:266px;width:938px;height:1px;background:#3a3a3a}
.footer .copy{position:absolute;left:0;top:309px;width:1200px;text-align:center;font-size:10px;color:#ccc}
</style>
</head>
<body>

<header class="hero">
  <div class="glow" role="img" aria-label="Hilltop Italian village with colourful houses beneath rocky cliffs at sunset"></div>
  <div class="brand" style="left:35px;top:24px;font-size:34px"><span class="mark"></span>StayNest</div>
  <nav class="nav">
    <a class="active" style="left:564px">HOME</a>
    <a style="left:643px">PROPERTY</a>
    <a style="left:761px">CUSTOM</a>
    <a style="left:858px">BLOG</a>
    <a style="left:925px">CONTACT US</a>
    <a class="cta">INFO REQUEST</a>
  </nav>
  <h1>EXCLUSIVE VILLAS IN ITALY</h1>
  <div class="field" style="left:141px;width:220px">DESTINATION
    <svg width="10" height="14" viewBox="0 0 10 14"><path d="M5 0a5 5 0 0 0-5 5c0 4 5 9 5 9s5-5 5-9a5 5 0 0 0-5-5zm0 7a2 2 0 1 1 0-4 2 2 0 0 1 0 4z" fill="#333"/></svg></div>
  <div class="field" style="left:371px;width:220px">CHECK IN
    <svg width="14" height="14" viewBox="0 0 14 14"><rect x="1" y="2" width="12" height="11" fill="none" stroke="#333" stroke-width="1.5"/><path d="M1 5h12M4 0v3M10 0v3" stroke="#333" stroke-width="1.5"/></svg></div>
  <div class="field" style="left:601px;width:221px">CHECK OUT
    <svg width="14" height="14" viewBox="0 0 14 14"><rect x="1" y="2" width="12" height="11" fill="none" stroke="#333" stroke-width="1.5"/><path d="M1 5h12M4 0v3M10 0v3" stroke="#333" stroke-width="1.5"/></svg></div>
  <div class="field" style="left:830px;width:222px">TRAVELERS
    <svg width="13" height="14" viewBox="0 0 13 14"><path d="M1 4l5.5 5.5L12 4" fill="none" stroke="#333" stroke-width="2.2"/></svg></div>
  <div class="search-btn">SEARCH</div>
  <div class="dots"><span></span><span></span><span class="on"></span><span></span><span></span></div>
</header>

<h2 class="section-title" style="top:716px">NEW VILLAS AND VACATION RENTALS</h2>
<div class="rule" style="left:577px;top:762px"></div>

<div class="arrow-box" style="left:65px"><svg width="9" height="12" viewBox="0 0 9 12"><path d="M7 1L2 6l5 5" fill="none" stroke="#999" stroke-width="1.5"/></svg></div>
<div class="arrow-box" style="left:1105px"><svg width="9" height="12" viewBox="0 0 9 12"><path d="M2 1l5 5-5 5" fill="none" stroke="#999" stroke-width="1.5"/></svg></div>

<article class="rental" style="left:132px">
  <div class="photo" role="img" aria-label="Modern white villa with palm trees and infinity pool" style="background:linear-gradient(180deg,#bcd3e6 0%,#e9eef1 45%,#2fb4d0 72%,#1990b4 100%)"></div>
  <h3>AGRITURISMO IL BIANCO</h3>
  <ul><li>Accommodations: 2</li><li>Sleeps: 7</li><li>Bedrooms: 2</li><li>Bathrooms: 2</li></ul>
  <span class="btn-small">VIEW DETAILS</span>
  <div class="price"><b>€ 3400</b><small>/ week</small></div>
</article>
<article class="rental" style="left:453px">
  <div class="photo" role="img" aria-label="Illuminated stone villa and pool at dusk" style="background:linear-gradient(180deg,#1c3050 0%,#3a4660 35%,#b48a3e 58%,#1f6f7e 80%,#12384a 100%)"></div>
  <h3>PODERE IL PINO</h3>
  <ul><li>Accommodations: 4</li><li>Sleeps: 27</li><li>Bedrooms: 10</li><li>Bathrooms: 6</li></ul>
  <span class="btn-small">VIEW DETAILS</span>
  <div class="price"><b>€ 3400</b><small>/ week</small></div>
</article>
<article class="rental" style="left:773px">
  <div class="photo" role="img" aria-label="Sunny villa terrace with pool and sun loungers" style="background:linear-gradient(180deg,#9fc4e6 0%,#e5d9c2 45%,#5cc1e0 72%,#e8e6e2 100%)"></div>
  <h3>VILLA 1</h3>
  <ul><li>Accommodations: 4</li><li>Sleeps: 27</li><li>Bedrooms: 10</li><li>Bathrooms: 6</li></ul>
  <span class="btn-small">VIEW DETAILS</span>
  <div class="price"><b>€ 3400</b><small>/ week</small></div>
</article>

<section class="holiday">
  <div class="photo" role="img" aria-label="Coastal Italian town on cliffs above turquoise sea with mountains" style="left:0;top:0;width:588px;height:532px;background:linear-gradient(180deg,#5d9fd9 0%,#bcd9ee 30%,#6f8a6a 52%,#c9a98a 62%,#1aa3b0 80%,#0e7d8f 100%)"></div>
  <h2>LOOKING FOR AN EXCLUSIVE HOLIDAY?</h2>
  <div class="rule"></div>
  <ul class="checks">
    <li style="top:8px"><svg width="13" height="10" viewBox="0 0 13 10"><path d="M1 5l4 4 7-8" fill="none" stroke="#1fae6b" stroke-width="2.4"/></svg>Browse our vacation rental selections</li>
    <li style="top:51px"><svg width="13" height="10" viewBox="0 0 13 10"><path d="M1 5l4 4 7-8" fill="none" stroke="#1fae6b" stroke-width="2.4"/></svg>If you are looking for a real experiences,<br>our portal is the right solution.</li>
    <li style="top:118px"><svg width="13" height="10" viewBox="0 0 13 10"><path d="M1 5l4 4 7-8" fill="none" stroke="#1fae6b" stroke-width="2.4"/></svg>Our vacation homes are all located in Italy and we<br>take care of them and their owners at every time. Our<br>goal is give to our guest authentic taste of holiday and<br>our country.</li>
    <li style="top:228px"><svg width="13" height="10" viewBox="0 0 13 10"><path d="M1 5l4 4 7-8" fill="none" stroke="#1fae6b" stroke-width="2.4"/></svg>Our team is always ready to assure the best time<br>and take care of you!</li>
    <li style="top:295px"><svg width="13" height="10" viewBox="0 0 13 10"><path d="M1 5l4 4 7-8" fill="none" stroke="#1fae6b" stroke-width="2.4"/></svg>Add a local experience to your stay with us: by diving<br>into our local "network" you can have the unique chance<br>to discover and travel our culture through the eye of a<br>local...!</li>
  </ul>
</section>

<div class="feature" style="left:134px;top:1856px">
  <div class="icon" style="top:38px"><svg width="40" height="40" viewBox="0 0 40 40"><path d="M4 20L20 6l16 14M9 16v18h22V16" fill="none" stroke="#fff" stroke-width="3"/><rect x="16" y="23" width="8" height="11" fill="#fff"/></svg></div>
  <h3>LUXURY VILLAS</h3>
  <p>This selection of properties includes all<br>the best rentals available. Most with<br>private swimming pool with chef and<br>maid services available.</p>
</div>
<div class="feature" style="left:606px;top:1856px">
  <div class="icon" style="top:38px"><svg width="40" height="40" viewBox="0 0 40 40"><rect x="4" y="12" width="32" height="22" rx="3" fill="#fff"/><path d="M14 12V7h12v5" fill="none" stroke="#fff" stroke-width="3"/><path d="M4 22h32" stroke="#1fae6b" stroke-width="2"/></svg></div>
  <h3>EXPERIENCES</h3>
  <p>Don't lve just a holiday but an experience!<br>Let's discover our services</p>
</div>
<div class="feature" style="left:134px;top:2042px">
  <div class="icon" style="top:37px"><svg width="40" height="40" viewBox="0 0 40 40"><path d="M4 22L18 10l14 12" fill="none" stroke="#fff" stroke-width="3"/><rect x="9" y="22" width="18" height="13" fill="#fff"/><path d="M30 4v12M26 7l4-3 5 3" fill="none" stroke="#fff" stroke-width="2"/></svg></div>
  <h3>BROWSE ALL VACATION RENTALS</h3>
  <p>From here you can browse all the villa<br>selections, you can refine them by using<br>the filters on the search results web page.</p>
</div>
<div class="feature" style="left:606px;top:2042px">
  <div class="icon" style="top:37px"><svg width="40" height="40" viewBox="0 0 40 40"><rect x="8" y="4" width="24" height="32" fill="#fff"/><path d="M14 27L26 13" stroke="#1fae6b" stroke-width="2.5"/><circle cx="15" cy="15" r="2.5" fill="#1fae6b"/><circle cx="25" cy="25" r="2.5" fill="#1fae6b"/></svg></div>
  <h3>LAST MINUTE DEALS</h3>
  <p>Browse all the last minute deals to browse the<br>villas offering discounts for last minute<br>arrivals. Save money by checking these offers.</p>
</div>

<div class="skyline" role="img" aria-label="Line drawing of Italian landmarks skyline"></div>

<section class="blog">
  <h2 class="section-title" style="top:46px">LATEST BLOG</h2>
  <div class="rule" style="left:577px;top:92px"></div>

  <article class="feature-post" role="img" aria-label="Italian villa with arched windows among cypress trees">
    <div class="shade"></div>
    <span class="date">April 02, 2021</span>
    <h3>LOREM IPSUM IS SIMPLY DUMMY TEXT OF THE PRINTING</h3>
    <p>Contrary to popular belief, Lorem Ipsum is not simply random text</p>
  </article>

  <article class="green-post">
    <div class="photo" role="img" aria-label="Villa with lit pool at night" style="background:linear-gradient(180deg,#25405e 0%,#3c5570 40%,#a07a44 62%,#2a7d98 82%,#163a52 100%)"></div>
    <h3>LOREM IPSUM IS SIMPLY DUMMY</h3>
    <p>There are many variations of passages of Lorem Ipsum available, but the majority have suffered alteration</p>
    <span class="btn-small">READ MORE</span>
  </article>

  <article class="post" style="left:132px;width:297px">
    <div class="photo" role="img" aria-label="Yellow villa behind a blue swimming pool" style="background:linear-gradient(180deg,#2f72c8 0%,#6a8c4e 40%,#c9b25a 58%,#1d7fd6 80%,#1a5fb0 100%)"></div>
    <span class="date">April 02, 2021</span>
    <h4>LOREM IPSUM IS SIMPLY DUMMY</h4>
    <p>There are many variations of passages of Lorem Ipsum available, but the.</p>
    <span class="btn-small">READ MORE</span>
  </article>
  <article class="post" style="left:452px;width:298px">
    <div class="photo" role="img" aria-label="Seaside terrace with pergola and pool" style="background:linear-gradient(180deg,#b9cfe3 0%,#d8c4a8 40%,#a2593f 58%,#5aa6c9 80%,#e3e0dc 100%)"></div>
    <span class="date">April 02, 2021</span>
    <h4>LOREM IPSUM IS SIMPLY DUMMY</h4>
    <p>There are many variations of passages of Lorem Ipsum available, but the.</p>
    <span class="btn-small">READ MORE</span>
  </article>
  <article class="post" style="left:773px;width:296px">
    <div class="photo" role="img" aria-label="Rustic games room with table tennis" style="background:linear-gradient(180deg,#4b3a2c 0%,#8a7a66 35%,#c8c0b2 60%,#5b6f86 80%,#6a5d52 100%)"></div>
    <span class="date">April 02, 2021</span>
    <h4>LOREM IPSUM IS SIMPLY DUMMY</h4>
    <p>There are many variations of passages of Lorem Ipsum available, but the.</p>
    <span class="btn-small">READ MORE</span>
  </article>
</section>

<footer class="footer">
  <div class="brand" style="left:131px;top:88px;font-size:42px;gap:14px"><span class="mark" style="width:50px;height:50px"></span>StayNest</div>

  <h5 style="left:509px">MENU</h5>
  <ul class="menu"><li>HOME</li><li>PROPERTY</li><li>CUSTOM</li><li>BLOG</li><li>CONTACT US</li></ul>

  <h5 style="left:681px">CONTACT US</h5>
  <div class="contact-row" style="left:681px;top:88px"><span class="dot"><svg width="11" height="11" viewBox="0 0 10 14"><path d="M5 0a5 5 0 0 0-5 5c0 4 5 9 5 9s5-5 5-9a5 5 0 0 0-5-5z" fill="#222"/></svg></span>via dei Cipressi 24<br>52100 Colle Alto, Arezzo (Italy)</div>
  <div class="contact-row" style="left:681px;top:139px"><span class="dot"><svg width="11" height="11" viewBox="0 0 12 12"><path d="M2 1l3 0 1 3-2 1a7 7 0 0 0 3 3l1-2 3 1v3c-6 0-10-4-10-10z" fill="#222"/></svg></span>Call Us<br>39 055 0100245</div>
  <div class="contact-row" style="left:681px;top:190px"><span class="dot"><svg width="11" height="11" viewBox="0 0 12 10"><rect x="0" y="1" width="12" height="8" fill="#222"/><path d="M0 1l6 5 6-5" fill="none" stroke="#fff" stroke-width="1"/></svg></span>E mail Us<br>hello@staynest-mail.com</div>

  <h5 style="left:960px">FOLLOW US</h5>
  <div class="contact-row" style="left:960px;top:88px"><span class="dot"></span>Like us on<br>OUR PAGE</div>
  <div class="contact-row" style="left:960px;top:139px"><span class="dot"></span>Follow us on<br>OUR FEED</div>
  <div class="contact-row" style="left:960px;top:190px"><span class="dot"></span>Follow us on<br>OUR NETWORK</div>

  <div class="divider"></div>
  <p class="copy">Copyright © 2021 All Rights Reserved</p>
</footer>

</body>
</html>
```